Calder Vane LED - E- Commerce site

We need a website designed for an LED Billboard company that sells:
1) LED Billboards (Sales & Rental)
2) LED Gas Station lights
3) Truss Systems (Sales & Rental)
4) Sound Systems (Sales & Rental)

Attached are websites that sell similar products as Calder Vane LED. Target market is for business, property managers and event coordinators.
This site will need to be an e-commerce site where customers can purchase the product directly from the site. What I'm looking for is a design layout to start.

Conceptual Web Designs:
http://192.0.2.47:8087/index.html
http://www.pmvdisplay.example/
http://www.auralomaaudio.example/
http://www.quillmarkpanel.example/

Attached is the logo of the company: Please note that the new spelling of the logo is "Calder Vane LED" using domain " CalderVaneLED.com

Industry/Entity Type

Gas Station

Number of Pages Required

5+ page

Requirements
Must have
• 1) E-Commerce - Customers will need to be able to order product from the site.
• 2) Customers will also have the option to rent the product as well.
Nice to have
• I like the image of the attached website, that has a video clip loop
• http://www.quillmarkpanel.example/

```html
<!DOCTYPE html>
<html lang="en">
<head>
<meta charset="utf-8">
<title>Calder Vane LED</title>
<link rel="stylesheet" href="https://fonts.googleapis.com/css2?family=Open+Sans:wght@400;600;700&family=Oswald:wght@400;500&display=swap">
<style>
:root{
  --red:#e3302c;
  --yellow:#fdc20f;
  --dark:#1b1b1b;
  --footer:#171717;
  --ink:#222;
  --muted:#777;
  --band:#e9e9e9;
  --line:#dcdcdc;
  --link:#2a7fd4;
}
*{box-sizing:border-box;margin:0;padding:0}
html,body{width:1200px;height:2214px;overflow:hidden}
body{font-family:"Open Sans",sans-serif;color:var(--ink);background:#fff;position:relative;font-size:13px}
a{color:inherit;text-decoration:none}
.wrap{position:relative;width:938px;margin:0 auto;height:100%}

/* header */
.topbar{height:136px;background:var(--dark);position:relative}
.brand{position:absolute;left:0;top:36px;display:flex;align-items:center;gap:12px}
.brand-dot{width:58px;height:58px;border-radius:50%;background:var(--yellow)}
.brand-name{font-weight:700;font-size:24px;color:var(--yellow);letter-spacing:.5px}
.util{position:absolute;right:0;top:12px;font-size:11px;color:#aaa;display:flex;gap:14px}
.util .sep{color:#666}
.util .phone{color:var(--red)}
.search{position:absolute;left:411px;top:60px;width:330px;height:42px;border:1px solid #3a3a3a;display:flex;align-items:center;padding:0 16px;font-size:11px;color:#666;font-style:italic}
.search svg{position:absolute;right:14px;top:12px}
.cart{position:absolute;right:0;top:60px;width:169px;height:42px;border:1px solid #3a3a3a;display:flex;align-items:center;gap:10px;padding-left:14px;color:#fff;font-size:12px}

.mainnav{height:47px;background:var(--red)}
.mainnav ul{list-style:none;display:flex;height:47px;align-items:stretch}
.mainnav li{display:flex;align-items:center;color:#fff;font-size:13px;text-transform:uppercase;padding:0 17px}
.mainnav li.active{background:var(--yellow);color:#222;padding:0 20px}
.mainnav li:nth-child(2){padding-left:23px}
.caret{display:inline-block;margin-left:8px;border:4px solid transparent;border-top-color:#fff;transform:translateY(2px)}

/* hero */
.hero{height:396px;position:relative;background:linear-gradient(180deg,#2b2d38,#4a3b3e 50%,#2a2c33)}
.hero-slide{position:absolute;left:0;top:30px;width:637px;height:333px;background:radial-gradient(circle at 65% 40%,#7fd3ff,#1b8fe0 55%,#0b5fb7)}
.hero-slide h2{position:absolute;left:22px;top:50px;font-family:"Oswald",sans-serif;font-weight:400;font-size:46px;color:#fff;letter-spacing:-.5px}
.hero-slide h2 span{color:var(--yellow)}
.hero-slide ul{position:absolute;left:22px;top:116px;list-style:none;color:#fff;font-size:14px;line-height:28px}
.panel-art{position:absolute;background:linear-gradient(135deg,#fafafa,#dfe4e8);border:3px solid #cfd5da}
.btn{display:inline-flex;align-items:center;justify-content:center;font-weight:700;font-size:11px;text-transform:uppercase;color:#222;background:var(--yellow)}
.btn.red{background:var(--red);color:#fff}
.hero-slide .actions{position:absolute;left:22px;top:215px;display:flex;gap:10px}
.hero-slide .actions .btn{width:102px;height:30px}
.arrows{position:absolute;right:26px;bottom:22px;display:flex;gap:2px}
.arrows span{width:31px;height:31px;background:var(--yellow);display:flex;align-items:center;justify-content:center}
.promo{position:absolute;left:651px;width:287px;overflow:hidden}
.promo h3{position:absolute;left:16px;font-family:"Oswald",sans-serif;font-weight:500;font-size:36px;line-height:1}
.promo .sub{position:absolute;left:16px;color:#fff;font-weight:700;font-size:15px}
.promo .txt{position:absolute;left:16px;color:#fff;font-size:12px}
.promo .off{position:absolute;font-family:"Oswald",sans-serif;font-size:28px;color:#fff}
.promo .off sup{font-size:13px}
.promo .btn{position:absolute;width:102px;height:28px}
.promo.sound{top:30px;height:156px;background:linear-gradient(90deg,#141418 40%,#3a3a42)}
.promo.sound h3{top:12px;color:#e3308a}
.promo.sound .sub{top:52px}
.promo.sound .txt{top:74px}
.promo.sound .btn{left:16px;top:116px}
.promo.sound .off{right:18px;top:110px}
.promo.sound .off b{color:#4fd3ff;font-weight:400}
.promo.truss{top:204px;height:159px;background:linear-gradient(135deg,#d02aa8,#9a2b9c 60%,#5a1e6e)}
.promo.truss h3{top:10px;color:#fff}
.promo.truss .sub{top:50px}
.promo.truss .txt{top:74px}
.promo.truss .off{left:16px;top:112px}
.promo.truss .off b{color:#4fd3ff;font-weight:400}
.promo.truss .btn{right:14px;top:116px}

/* featured */
.featured{height:809px;position:relative}
.section-title{font-size:17px;font-weight:600;letter-spacing:.4px;text-transform:uppercase;color:#222}
.featured .section-title{position:absolute;left:0;top:36px}
.filters{position:absolute;right:-10px;top:33px;display:flex;font-size:11px;color:#666;text-transform:uppercase}
.filters span{padding:7px 12px}
.filters .on{background:#ddd;color:#222}
.grid{position:absolute;left:0;top:96px;display:grid;grid-template-columns:repeat(4,218px);column-gap:22px;row-gap:19px}
.card{height:336px;border:1px solid var(--line);text-align:center}
.card .art{height:188px;border-bottom:1px solid var(--line)}
.card h4{font-size:12.5px;font-weight:700;margin-top:17px}
.card p{font-size:11.5px;color:var(--muted);line-height:17px;margin:8px 20px 0}
.card .actions{display:flex;justify-content:center;gap:4px;margin-top:10px}
.card .actions .btn{width:92px;height:34px}

/* features */
.features{height:156px;background:var(--band)}
.features .cols{display:grid;grid-template-columns:repeat(4,218px);column-gap:22px;padding-top:26px}
.feat h5{display:flex;align-items:center;gap:8px;font-size:15px;font-weight:700;letter-spacing:.3px;text-transform:uppercase}
.feat p{font-size:11px;color:#888;line-height:18px;margin-top:12px;width:190px}
.feat a{font-size:11px;color:var(--link)}

/* about */
.about{height:270px;position:relative}
.about .col-a{position:absolute;left:0;top:36px;width:440px}
.about .col-a p{font-size:12.5px;color:#777;line-height:20px;margin-top:18px}
.about .col-a p+p{margin-top:2px}
.about .col-b{position:absolute;left:493px;top:36px;width:445px}
.certs{display:grid;grid-template-columns:repeat(3,1fr);column-gap:20px;row-gap:26px;margin-top:28px}
.cert{height:44px;border-radius:6px;background:#d9d9d9}

/* signup */
.signup{height:89px;background:var(--band)}
.signup .row{display:flex;align-items:center;height:89px}
.signup label{font-size:14px;font-weight:700;letter-spacing:.3px;text-transform:uppercase;width:170px}
.signup .field{width:254px;height:34px;background:#fff;font-size:11px;color:#999;font-style:italic;display:flex;align-items:center;padding-left:14px}
.signup .btn{width:99px;height:34px}
.signup .divider{width:1px;height:44px;background:#ccc;margin:0 40px}
.signup .stay{font-size:14px;font-weight:700;letter-spacing:.3px;text-transform:uppercase}
.social{display:flex;gap:12px;margin-left:auto}
.social span{width:34px;height:34px}

/* footer */
.footer{height:311px;background:var(--footer);color:#bbb;position:relative}
.fcol{position:absolute;top:30px}
.fcol h6{color:var(--yellow);font-size:13px;font-weight:700;text-transform:uppercase;margin-bottom:18px}
.fcol li{list-style:none;font-size:11.5px;line-height:24.5px}
.contact-row{display:flex;gap:14px;font-size:11.5px;line-height:19px;margin-bottom:12px}
.contact-row svg{flex:none;margin-top:2px}
.bottom{position:absolute;left:0;right:0;top:255px;border-top:1px solid #2a2a2a}
.bottom .wrap{display:flex;align-items:center;height:56px;font-size:11px;color:#aaa}
.pay{margin-left:auto;display:flex;align-items:center;gap:10px}
.pay span{width:34px;height:22px;border-radius:11px;background:#555}
</style>
</head>
<body>

<header class="topbar">
  <div class="wrap">
    <div class="brand"><span class="brand-dot"></span><span class="brand-name">Calder Vane LED</span></div>
    <div class="util">
      <span>CUSTOMER SERVICE: <span class="phone">+1 555 010 4477</span></span><span class="sep">|</span>
      <span>MY ACCOUNT</span><span class="sep">|</span>
      <span>WISH LIST (0)</span><span class="sep">|</span>
      <span>CHECKOUT</span><span class="sep">|</span>
      <span>LOGIN</span>
    </div>
    <div class="search">SEARCH HERE...
      <svg width="16" height="16" viewBox="0 0 16 16"><circle cx="6.5" cy="6.5" r="5" fill="none" stroke="#e3302c" stroke-width="2"/><line x1="10.5" y1="10.5" x2="15" y2="15" stroke="#e3302c" stroke-width="2"/></svg>
    </div>
    <div class="cart">
      <svg width="26" height="22" viewBox="0 0 26 22"><path d="M1 2h4l3 12h13l3-9H7" fill="none" stroke="#fdc20f" stroke-width="2"/><circle cx="10" cy="19" r="2" fill="#fdc20f"/><circle cx="19" cy="19" r="2" fill="#fdc20f"/></svg>
      <span>0 ITEM(S) - $0.00</span>
    </div>
  </div>
</header>

<nav class="mainnav">
  <div class="wrap">
    <ul>
      <li class="active">Home</li>
      <li>LED Lights Systems<span class="caret"></span></li>
      <li>Truss Systems</li>
      <li>Sound Systems</li>
      <li>Service and Support</li>
      <li>About</li>
      <li>Contact Us</li>
    </ul>
  </div>
</nav>

<section class="hero" role="img" aria-label="Blurred night street scene with illuminated billboards">
  <div class="wrap">
    <div class="hero-slide">
      <h2><span>LED</span> PANEL LIGHT</h2>
      <ul>
        <li>- ENVIRONMENTAL PROTECTION</li>
        <li>- ENERGY SAVING</li>
        <li>- GREEN LIGHTING</li>
      </ul>
      <div class="panel-art" role="img" aria-label="Square LED panel light" style="left:437px;top:70px;width:150px;height:190px"></div>
      <div class="panel-art" role="img" aria-label="Rectangular LED panel light" style="left:268px;top:190px;width:260px;height:115px"></div>
      <div class="actions"><span class="btn">Buy Now!</span><span class="btn red">On Rent</span></div>
      <div class="arrows">
        <span><svg width="8" height="12" viewBox="0 0 8 12"><path d="M6 1L1 6l5 5" fill="none" stroke="#fff" stroke-width="2"/></svg></span>
        <span><svg width="8" height="12" viewBox="0 0 8 12"><path d="M2 1l5 5-5 5" fill="none" stroke="#fff" stroke-width="2"/></svg></span>
      </div>
    </div>
    <div class="promo sound" role="img" aria-label="Loudspeaker close-up">
      <h3>SOUND</h3>
      <div class="sub">SYSTEMS</div>
      <div class="txt">SIMPLY DUMMY PRINTING</div>
      <span class="btn">Buy Now!</span>
      <div class="off"><b>25</b><sup>%</sup>OFF</div>
    </div>
    <div class="promo truss" role="img" aria-label="Stage truss with moving lights">
      <h3>TRUSS</h3>
      <div class="sub">SYSTEMS</div>
      <div class="txt">SIMPLY DUMMY PRINTING</div>
      <div class="off"><b>25</b><sup>%</sup>OFF</div>
      <span class="btn">Buy Now!</span>
    </div>
  </div>
</section>

<section class="featured">
  <div class="wrap">
    <h2 class="section-title">Featured Products</h2>
    <div class="filters"><span class="on">All</span><span>LED Light</span><span>Gas Station Light</span><span>Truss Systems</span><span>Sound Systems</span></div>
    <div class="grid">
      <article class="card"><div class="art" role="img" aria-label="White recessed LED spotlight" style="background:radial-gradient(circle,#eeeeee 30%,#fff 70%)"></div><h4>30W-LED Panel Light</h4><p>simply dummy text the printing and typesetting industry</p><div class="actions"><span class="btn">Buy Now</span><span class="btn red">On Rent</span></div></article>
      <article class="card"><div class="art" role="img" aria-label="T8 LED tube" style="background:linear-gradient(150deg,#fff 30%,#e8ecee 50%,#fff 70%)"></div><h4>20W-T8-LED Tube-UL</h4><p>simply dummy text the printing and typesetting industry</p><div class="actions"><span class="btn">Buy Now</span><span class="btn red">On Rent</span></div></article>
      <article class="card"><div class="art" role="img" aria-label="Portable USB sound system" style="background:radial-gradient(circle,#3a3a3a 30%,#fff 60%)"></div><h4>Sistema Sonido Portatil USB</h4><p>simply dummy text the printing and typesetting industry</p><div class="actions"><span class="btn">Buy Now</span><span class="btn red">On Rent</span></div></article>
      <article class="card"><div class="art" role="img" aria-label="Stage light on truss arch" style="background:radial-gradient(circle,#4a4a4a 25%,#ddd 45%,#fff 65%)"></div><h4>DJ Truss arch</h4><p>simply dummy text the printing and typesetting industry</p><div class="actions"><span class="btn">Buy Now</span><span class="btn red">On Rent</span></div></article>
      <article class="card"><div class="art" role="img" aria-label="DJ mixing controller" style="background:radial-gradient(ellipse,#2d2d2d 30%,#fff 60%)"></div><h4>Vantor DECKMIX FOUR</h4><p>simply dummy text the printing and typesetting industry</p><div class="actions"><span class="btn">Buy Now</span><span class="btn red">On Rent</span></div></article>
      <article class="card"><div class="art" role="img" aria-label="Square ceiling LED panel" style="background:radial-gradient(circle,#ecebe4 35%,#fff 65%)"></div><h4>30W-LED Panel Light</h4><p>simply dummy text the printing and typesetting industry</p><div class="actions"><span class="btn">Buy Now</span><span class="btn red">On Rent</span></div></article>
      <article class="card"><div class="art" role="img" aria-label="DJ table on truss stand" style="background:radial-gradient(ellipse,#9a9a9a 20%,#fff 60%)"></div><h4>DJ Tables &amp; Stands</h4><p>simply dummy text the printing and typesetting industry</p><div class="actions"><span class="btn">Buy Now</span><span class="btn red">On Rent</span></div></article>
      <article class="card"><div class="art" role="img" aria-label="Two T5 LED tubes" style="background:linear-gradient(150deg,#fff 30%,#e6ebf0 50%,#fff 70%)"></div><h4>GlowLine T5 LED</h4><p>simply dummy text the printing and typesetting industry</p><div class="actions"><span class="btn">Buy Now</span><span class="btn red">On Rent</span></div></article>
    </div>
  </div>
</section>

<section class="features">
  <div class="wrap">
    <div class="cols">
      <div class="feat"><h5><svg width="20" height="20" viewBox="0 0 20 20"><circle cx="10" cy="10" r="7" fill="none" stroke="#222" stroke-width="4" stroke-dasharray="3 2.5"/><circle cx="10" cy="10" r="5" fill="#222"/><circle cx="10" cy="10" r="2" fill="#e9e9e9"/></svg>Technology</h5><p>t is long established fact the reader will be distracted by the readable content of a page...</p><a>Read More »</a></div>
      <div class="feat"><h5><svg width="20" height="20" viewBox="0 0 20 20"><circle cx="5" cy="5" r="3" fill="none" stroke="#222" stroke-width="2.5"/><circle cx="15" cy="15" r="3" fill="none" stroke="#222" stroke-width="2.5"/><line x1="16" y1="2" x2="4" y2="18" stroke="#222" stroke-width="2.5"/></svg>Price</h5><p>t is long established fact the reader will be distracted by the readable content of a page...</p><a>Read More »</a></div>
      <div class="feat"><h5><svg width="20" height="20" viewBox="0 0 20 20"><rect x="2" y="4" width="14" height="14" fill="none" stroke="#222" stroke-width="2"/><path d="M5 10l4 4 9-11" fill="none" stroke="#222" stroke-width="3"/></svg>Quality</h5><p>t is long established fact the reader will be distracted by the readable content of a page...</p><a>Read More »</a></div>
      <div class="feat"><h5><svg width="20" height="20" viewBox="0 0 20 20"><circle cx="10" cy="10" r="8.5" fill="none" stroke="#222" stroke-width="2"/><path d="M10 4l1.8 3.8 4 .4-3 2.8.9 4-3.7-2.1-3.7 2.1.9-4-3-2.8 4-.4z" fill="#222"/></svg>Warranty</h5><p>t is long established fact the reader will be distracted by the readable content of a page...</p><a>Returns Policy »</a></div>
    </div>
  </div>
</section>

<section class="about">
  <div class="wrap">
    <div class="col-a">
      <h2 class="section-title">About Calder Vane LED</h2>
      <p>It is a long established fact that a reader will be distracted by the readable content of a page when looking at its layout. The point of using Lorem Ipsum is that it has a more-or-less normal distribution of Content here, content here, making it look like readable English.</p>
      <p>Many desktop publishing packages and web page editors now use Lorem Ipsum as their default model text, and a search for 'lorem ipsum' will uncover many web sites still in their infancy...</p>
    </div>
    <div class="col-b">
      <h2 class="section-title">Product Certification</h2>
      <div class="certs">
        <div class="cert"></div><div class="cert"></div><div class="cert"></div>
        <div class="cert"></div><div class="cert"></div><div class="cert"></div>
      </div>
    </div>
  </div>
</section>

<section class="signup">
  <div class="wrap">
    <div class="row">
      <label>Sign up for deals:</label>
      <div class="field">Enter Your Email</div>
      <span class="btn">Sign Up</span>
      <span class="divider"></span>
      <span class="stay">Stay Connected:</span>
      <div class="social">
        <span style="background:#3b5998"></span>
        <span style="background:#1da1f2"></span>
        <span style="background:#0e76a8"></span>
        <span style="background:#dd4b39"></span>
      </div>
    </div>
  </div>
</section>

<footer class="footer">
  <div class="wrap">
    <div class="fcol" style="left:0"><h6>Quick Links</h6><ul><li>Home</li><li>Products</li><li>Services</li><li>About Us</li><li>FAQ's</li></ul></div>
    <div class="fcol" style="left:160px"><h6>Need Help?</h6><ul><li>See All Help</li><li>Returns</li><li>Shipping</li><li>Warranty</li><li>Contact Us</li></ul></div>
    <div class="fcol" style="left:332px"><h6>Policies &amp; Info</h6><ul><li>Terms and Conditions</li><li>Policy for Sellers</li><li>Policy for Buyers</li><li>Shipping &amp; Refund Policies</li><li>Wholesale Policy</li><li>Privacy Policy</li></ul></div>
    <div class="fcol" style="left:546px"><h6>My Account</h6><ul><li>Sign in</li><li>Track Order</li></ul></div>
    <div class="fcol" style="left:732px;width:206px"><h6>Contact Us</h6>
      <div class="contact-row"><svg width="12" height="16" viewBox="0 0 12 16"><path d="M6 0a6 6 0 0 0-6 6c0 4.5 6 10 6 10s6-5.5 6-10a6 6 0 0 0-6-6z" fill="#777"/><circle cx="6" cy="6" r="2" fill="#171717"/></svg><span>Lorem Ipsum is simply dummy<br>Riverton, AB T0X 2K4</span></div>
      <div class="contact-row"><svg width="12" height="14" viewBox="0 0 12 14"><path d="M2 0l3 3-1.5 2a8 8 0 0 0 4 4.5L9.5 8l2.5 3-2 2.5C4 12 0 7 .5 2z" fill="#777"/></svg><span>Phone:<br>(555) 010 4477</span></div>
      <div class="contact-row"><svg width="12" height="10" viewBox="0 0 12 10"><rect width="12" height="10" fill="#777"/><path d="M0 0l6 5 6-5" fill="none" stroke="#171717" stroke-width="1.2"/></svg><span>Email:<br>info@caldervaneled.com</span></div>
    </div>
  </div>
  <div class="bottom">
    <div class="wrap">
      <span>Copyright © 2016 - Calder Vane LED, All Rights Reserved</span>
      <div class="pay">Accepted Payment : <span></span><span></span><span></span><span></span></div>
    </div>
  </div>
</footer>

</body>
</html>
```